Website for Dental Office - The Bright Arch Clinic

The bright arch clinic is a dental office offering cosmetic dentistry, general dentistry, and multi-specialty dental care all under one roof in our state-of-the-art cosmetic dental center. We are particularly striving to provide services that fit the need of the young generation. Thus, we hope to have a modern, professional concise website that represents our spirit.

*Should be able to switch from English to Chinese

6 sections besides homepage:
Home, Meet us, Services,
Patient Info, Cases&Reviews, Blog, Contact

The Services sections should contain multiple subsections such as cleaning and prevention, cosmetic dentistry, implant dentistry, removable dentures, etc...
The Patient Info section is also intended to contain several subsections such as
New Patient offer, accepted Insurance, patient portal, helpful tips, etc...

Target Market(s)

young generation

Coding

Coded - Design and coding required

Number of Pages Required

5+ page

Font styles to use
Sans Serif

Colors
0592cd
33a6d7
85cae6
00a990
33b8a4
86cfc6
cee9f5
cfeae6
3277b5

Requirements
Must have
• *Should be able to switch from English to Chinese
Nice to have
• http://www.thebrightarchclinic.com/
• As a reference, the above link is the current website, but we would like to change the appearance and the content (our new logo's picture is attached)

```html
<!DOCTYPE html>
<html lang="en">
<head>
<meta charset="utf-8">
<title>The Bright Arch Clinic</title>
<link href="https://fonts.googleapis.com/css2?family=Questrial&family=Nunito+Sans:wght@400;700;800;900&display=swap" rel="stylesheet">
<style>
:root{
  --blue-deep:#1a78c2;
  --blue-main:#0592cd;
  --blue-mid:#33a6d7;
  --blue-soft:#85cae6;
  --blue-pale:#cee9f5;
  --teal:#00a990;
  --teal-mid:#33b8a4;
  --teal-soft:#86cfc6;
  --navy:#3277b5;
  --ink:#333a40;
  --white:#ffffff;
  --page-pale:#eef6fb;
}
*{margin:0;padding:0;box-sizing:border-box}
html,body{width:1200px;height:2596px;overflow:hidden}
body{font-family:"Questrial",sans-serif;color:var(--ink);background:var(--white);position:relative}
.heading{font-family:"Nunito Sans",sans-serif;font-weight:900;letter-spacing:.5px}

/* header */
.site-header{position:absolute;top:0;left:0;width:1200px;height:119px;border-bottom:1px solid #e3e8ec;background:var(--white)}
.brand{position:absolute;left:145px;top:40px;display:flex;align-items:center;gap:10px;font-family:"Nunito Sans",sans-serif;font-weight:800;font-size:18px;color:var(--blue-main)}
.brand-mark{width:26px;height:26px;background:var(--blue-mid);border-radius:4px}
.call{position:absolute;right:235px;top:22px;font-size:20px;color:var(--blue-main);display:flex;align-items:center;gap:8px}
.call b{font-family:"Nunito Sans",sans-serif;font-weight:800}
.lang{position:absolute;right:145px;top:27px;display:flex;align-items:center;gap:6px}
.lang-flag{width:32px;height:18px;background:var(--navy);border:1px solid #ccd}
.main-nav{position:absolute;right:145px;top:74px;display:flex;gap:34px;font-size:14px;text-transform:uppercase}
.main-nav a{color:var(--ink);text-decoration:none}
.main-nav a.active{color:var(--blue-main);font-weight:700}

/* hero */
.hero{position:absolute;top:119px;left:0;width:1200px;height:580px;background:linear-gradient(90deg,#8cc6e8 0%,#a8cde3 40%,#c9cfd8 62%,#d9c6cf 80%,#c8b4bd 100%)}
.hero-title{position:absolute;left:145px;top:130px;color:var(--white)}
.hero-title .line-1{font-size:52px;letter-spacing:1px;line-height:1}
.hero-title .line-2{font-family:"Nunito Sans",sans-serif;font-weight:900;font-size:74px;line-height:1;margin-top:20px}
.hero-btn{position:absolute;left:145px;top:316px;width:219px;height:58px;border:2px solid var(--white);border-radius:30px;color:var(--white);font-size:20px;display:flex;align-items:center;justify-content:center;font-family:"Nunito Sans",sans-serif;font-weight:700}
.slider-dots{position:absolute;left:569px;top:498px;display:flex;gap:4px}
.slider-dots span{width:13px;height:13px;border:2px solid var(--white);border-radius:50%}
.slider-dots span.on{background:var(--white)}

/* intro */
.intro{position:absolute;top:699px;left:0;width:1200px;height:450px;text-align:center}
.intro h1{margin-top:66px;font-size:38px;color:var(--blue-main)}
.intro p{width:870px;margin:26px auto 0;font-size:13px;line-height:21.5px}
.intro p + p{margin-top:15px}
.btn-solid{display:inline-flex;align-items:center;justify-content:center;margin-top:47px;width:214px;height:56px;border-radius:30px;background:var(--blue-deep);color:var(--white);font-family:"Nunito Sans",sans-serif;font-weight:800;font-size:14px}

/* services */
.services{position:absolute;top:1149px;left:0;width:1200px;height:574px;background:linear-gradient(135deg,#3aa0d7,#2f8fcb 60%,#3a9bd6);text-align:center;color:var(--white)}
.services h2{margin-top:58px;font-size:38px}
.service-grid{position:absolute;top:152px;left:140px;width:920px;display:flex;justify-content:space-between}
.service{width:200px;display:flex;flex-direction:column;align-items:center}
.service h3{font-family:"Nunito Sans",sans-serif;font-weight:700;font-size:15px;margin-top:18px}
.service p{font-size:11.5px;line-height:19px;margin-top:16px;height:78px}
.btn-white{margin-top:22px;width:128px;height:42px;border-radius:22px;background:var(--white);color:var(--blue-main);font-family:"Nunito Sans",sans-serif;font-weight:800;font-size:12px;display:flex;align-items:center;justify-content:center}
.btn-white.hot{background:var(--blue-soft);color:var(--white)}

/* patient info */
.patient-info{position:absolute;top:1723px;left:0;width:1200px;height:589px;background:var(--page-pale);text-align:center}
.patient-info h2{margin-top:66px;font-size:38px;color:var(--blue-main)}
.info-grid{position:absolute;top:153px;left:140px;width:920px;display:flex;justify-content:space-between}
.info-card{width:190px;display:flex;flex-direction:column;align-items:center}
.info-card h3{font-family:"Nunito Sans",sans-serif;font-weight:700;font-size:15px;margin-top:18px}
.info-card p{font-size:11.5px;line-height:19px;margin-top:16px;width:180px}
.btn-line{margin-top:22px;width:128px;height:42px;border-radius:22px;border:1.5px solid var(--blue-mid);color:var(--blue-mid);font-family:"Nunito Sans",sans-serif;font-weight:800;font-size:12px;display:flex;align-items:center;justify-content:center;background:var(--white)}
.btn-line.teal{border-color:var(--teal-mid);color:var(--teal)}
.btn-line.muted{border-color:var(--blue-soft);color:var(--blue-soft)}

/* footer */
.site-footer{position:absolute;top:2312px;left:0;width:1200px;height:284px;background:var(--blue-deep);color:var(--white)}
.foot-title{position:absolute;top:46px;font-family:"Nunito Sans",sans-serif;font-weight:800;font-size:14px;letter-spacing:.5px}
.foot-list{position:absolute;top:88px;list-style:none;font-size:13px;line-height:28px}
.contact-row{position:absolute;left:576px;font-size:13px;display:flex;gap:6px;line-height:16px}
.social li{display:flex;align-items:center;gap:6px}
.social .dot{width:11px;height:11px;background:var(--white);border-radius:2px}
.foot-rule{position:absolute;left:145px;top:233px;width:910px;height:1px;background:rgba(255,255,255,.3)}
.copyright{position:absolute;left:145px;top:252px;font-size:12.5px}
.legal{position:absolute;left:867px;top:252px;font-size:10px;color:var(--blue-soft)}
.code{position:absolute;left:1103px;top:252px;font-size:12.5px}
</style>
</head>
<body>

<header class="site-header">
  <div class="brand"><span class="brand-mark"></span>The Bright Arch Clinic</div>
  <div class="call">
    <svg width="16" height="16" viewBox="0 0 24 24"><path fill="#0592cd" d="M6.6 10.8a15.1 15.1 0 0 0 6.6 6.6l2.2-2.2c.3-.3.7-.4 1-.2 1.1.4 2.3.6 3.6.6.6 0 1 .4 1 1V20c0 .6-.4 1-1 1A17 17 0 0 1 3 4c0-.6.4-1 1-1h3.5c.6 0 1 .4 1 1 0 1.3.2 2.5.6 3.6.1.3 0 .7-.2 1z"/></svg>
    Call Us: <b>555.204.7180</b>
  </div>
  <div class="lang"><span class="lang-flag"></span>
    <svg width="9" height="6" viewBox="0 0 9 6"><path d="M0 0h9L4.5 6z" fill="#333a40"/></svg>
  </div>
  <nav class="main-nav">
    <a class="active" href="#">Home</a><a href="#">Meet us</a><a href="#">Services</a><a href="#">Patient info</a><a href="#">Cases&amp;Reviews</a><a href="#">Blog</a><a href="#">Contact</a>
  </nav>
</header>

<section class="hero" role="img" aria-label="Close-up photo of a bright, healthy smile">
  <div class="hero-title">
    <div class="line-1">THE BRIGHT ARCH</div>
    <div class="line-2">CLINIC</div>
  </div>
  <div class="hero-btn">GET MORE INFO</div>
  <div class="slider-dots"><span class="on"></span><span></span><span></span><span></span></div>
</section>

<section class="intro">
  <h1 class="heading">YOUR SMILE. OUR PASSION.</h1>
  <p>Welcome to The Bright Arch Clinic where we specialize in General and Cosmetic Dentistry, Dental Implants, Periodontics (Gum Surgery), Endodontics (Root Canal Treatment) and Reconstructive Dentistry for patients in Boston, Brookline, Cambridge, Brighton, Allston, Newton, Watertown, Wellesley and all other surrounding neighborhoods of Boston, Massachusetts.</p>
  <p>With Northgate and Eastvale credentials that inspire confidence, we offer cosmetic dentistry, general dentistry and multi-specialty dental care all under one roof in our state-of-the-art cosmetic dental center conveniently located near Linden Square on Harbor Avenue steps from the metro. Our specialist are also trained in providing wrinkle relaxers and Dermal Fillers and we would be honored to have you a part of our growing family.</p>
  <div class="btn-solid">REQUEST APPOINTMENT</div>
</section>

<section class="services">
  <h2 class="heading">OUR SERVICES</h2>
  <div class="service-grid">
    <div class="service">
      <svg width="152" height="155" viewBox="0 0 152 155" role="img" aria-label="Icon of a tooth under a magnifying glass"><path d="M6 0h140a6 6 0 0 1 6 6v149Q76 105 0 155V6a6 6 0 0 1 6-6z" fill="#ffffff"/></svg>
      <h3>Cleaning and Prevention</h3>
      <p>Professional dental cleanings (oral prophylaxis) are usually performed by the dentist or a registered dental hygienist</p>
      <div class="btn-white">LEARN MORE</div>
    </div>
    <div class="service">
      <svg width="152" height="155" viewBox="0 0 152 155" role="img" aria-label="Icon of a smiling mouth with teeth"><path d="M6 0h140a6 6 0 0 1 6 6v149Q76 105 0 155V6a6 6 0 0 1 6-6z" fill="#ffffff"/></svg>
      <h3>Cosmetic Dentistry</h3>
      <p>Veneers are very thin pieces of durable, tooth shaped porcelain that are custom made and onded onto the front of teeth</p>
      <div class="btn-white">LEARN MORE</div>
    </div>
    <div class="service">
      <svg width="152" height="155" viewBox="0 0 152 155" role="img" aria-label="Icon of a dental implant"><path d="M6 0h140a6 6 0 0 1 6 6v149Q76 105 0 155V6a6 6 0 0 1 6-6z" fill="#85cae6"/></svg>
      <h3>Implant Dentistry</h3>
      <p>Dental implants are a great way to replace missing teeth and also provide a fixed solution to having removable partial or complete</p>
      <div class="btn-white hot">LEARN MORE</div>
    </div>
    <div class="service">
      <svg width="152" height="155" viewBox="0 0 152 155" role="img" aria-label="Icon of a removable denture"><path d="M6 0h140a6 6 0 0 1 6 6v149Q76 105 0 155V6a6 6 0 0 1 6-6z" fill="#ffffff"/></svg>
      <h3>Removable Dentures</h3>
      <p>Removable partial dentures are used when only a few teeth are missing and there are still natural teeth present in the mouth.</p>
      <div class="btn-white">LEARN MORE</div>
    </div>
  </div>
</section>

<section class="patient-info">
  <h2 class="heading">PATIENT INFO</h2>
  <div class="info-grid">
    <div class="info-card">
      <svg width="160" height="162" viewBox="0 0 160 162" role="img" aria-label="Photo of a mother and daughter smiling"><defs><linearGradient id="g1" x1="0" y1="0" x2="1" y2="1"><stop offset="0" stop-color="#f3e4dc"/><stop offset="1" stop-color="#d9b8a8"/></linearGradient></defs><path d="M8 0h144a8 8 0 0 1 8 8v154Q80 112 0 162V8a8 8 0 0 1 8-8z" fill="#85cae6"/><path d="M10 3h140a7 7 0 0 1 7 7v145Q80 108 3 155V10a7 7 0 0 1 7-7z" fill="url(#g1)"/></svg>
      <h3>New Patient offer</h3>
      <p>Thank you for your trust in us. We look forward to working with you towards a healthy and beautiful smile.</p>
      <div class="btn-line">LEARN MORE</div>
    </div>
    <div class="info-card">
      <svg width="160" height="162" viewBox="0 0 160 162" role="img" aria-label="Photo of wooden blocks labelled insurance"><defs><linearGradient id="g2" x1="0" y1="0" x2="1" y2="1"><stop offset="0" stop-color="#3a2f28"/><stop offset="1" stop-color="#b89468"/></linearGradient></defs><path d="M8 0h144a8 8 0 0 1 8 8v154Q80 112 0 162V8a8 8 0 0 1 8-8z" fill="#33b8a4"/><path d="M10 3h140a7 7 0 0 1 7 7v145Q80 108 3 155V10a7 7 0 0 1 7-7z" fill="url(#g2)"/></svg>
      <h3>Accepted Insurance</h3>
      <p>Thank you for your trust in us. We look forward to working with you towards a healthy and beautiful smile.</p>
      <div class="btn-line teal">LEARN MORE</div>
    </div>
    <div class="info-card">
      <svg width="160" height="162" viewBox="0 0 160 162" role="img" aria-label="Photo of a patient at a dental check-up"><defs><linearGradient id="g3" x1="0" y1="0" x2="1" y2="1"><stop offset="0" stop-color="#e8ecef"/><stop offset="1" stop-color="#b98c78"/></linearGradient></defs><path d="M8 0h144a8 8 0 0 1 8 8v154Q80 112 0 162V8a8 8 0 0 1 8-8z" fill="#cee9f5"/><path d="M10 3h140a7 7 0 0 1 7 7v145Q80 108 3 155V10a7 7 0 0 1 7-7z" fill="url(#g3)"/></svg>
      <h3>Patient Portal</h3>
      <p>Thank you for your trust in us. We look forward to working with you towards a healthy and beautiful smile.</p>
      <div class="btn-line muted">LEARN MORE</div>
    </div>
    <div class="info-card">
      <svg width="160" height="162" viewBox="0 0 160 162" role="img" aria-label="Photo of a dental model of teeth and gums"><defs><linearGradient id="g4" x1="0" y1="0" x2="1" y2="1"><stop offset="0" stop-color="#e6eef2"/><stop offset="1" stop-color="#e48c92"/></linearGradient></defs><path d="M8 0h144a8 8 0 0 1 8 8v154Q80 112 0 162V8a8 8 0 0 1 8-8z" fill="#86cfc6"/><path d="M10 3h140a7 7 0 0 1 7 7v145Q80 108 3 155V10a7 7 0 0 1 7-7z" fill="url(#g4)"/></svg>
      <h3>Helpful Tips</h3>
      <p>Thank you for your trust in us. We look forward to working with you towards a healthy and beautiful smile.</p>
      <div class="btn-line teal">LEARN MORE</div>
    </div>
  </div>
</section>

<footer class="site-footer">
  <div class="foot-title" style="left:145px">QUICK LINKS</div>
  <ul class="foot-list" style="left:145px"><li>Home</li><li>Meet us</li><li>Services</li><li>Patient Info</li></ul>
  <ul class="foot-list" style="left:369px"><li>Cases&amp;Reviews</li><li>Blog</li><li>Contact</li></ul>

  <div class="foot-title" style="left:576px">CONTACT INFO</div>
  <div class="contact-row" style="top:95px">
    <svg width="11" height="15" viewBox="0 0 12 16"><path fill="#fff" d="M6 0a6 6 0 0 0-6 6c0 4.5 6 10 6 10s6-5.5 6-10a6 6 0 0 0-6-6zm0 8.5A2.5 2.5 0 1 1 6 3.5a2.5 2.5 0 0 1 0 5z"/></svg>
    <span>270 Harbor Avenue, Suite 12,<br>Fairview MA 02199</span>
  </div>
  <div class="contact-row" style="top:145px">
    <svg width="12" height="12" viewBox="0 0 24 24"><path fill="#fff" d="M6.6 10.8a15.1 15.1 0 0 0 6.6 6.6l2.2-2.2c.3-.3.7-.4 1-.2 1.1.4 2.3.6 3.6.6.6 0 1 .4 1 1V20c0 .6-.4 1-1 1A17 17 0 0 1 3 4c0-.6.4-1 1-1h3.5c.6 0 1 .4 1 1 0 1.3.2 2.5.6 3.6.1.3 0 .7-.2 1z"/></svg>
    <span>555.204.7180</span>
  </div>
  <div class="contact-row" style="top:173px">
    <svg width="13" height="10" viewBox="0 0 26 20"><path fill="#fff" d="M0 0h26v20H0zM2 2l11 9 11-9z"/></svg>
    <span>info@thebrightarchclinic.com</span>
  </div>

  <div class="foot-title" style="left:926px">CONNECT WITH US</div>
  <ul class="foot-list social" style="left:926px">
    <li><span class="dot"></span>Birdfeed</li>
    <li><span class="dot"></span>Socialbook</li>
    <li><span class="dot"></span>Snapgram</li>
    <li><span class="dot"></span>Circleplus</li>
  </ul>

  <div class="foot-rule"></div>
  <div class="copyright">Copyrights © 2019 The Bright Arch Clinic. All rights reserved.</div>
  <div class="legal">Terms and Conditions | Privacy Policy</div>
  <div class="code">C16</div>
</footer>

</body>
</html>
```